Veltra Metrics New Website for Health Benefits Plan Decisioneering Tool Launch

Veltra Metrics is a SaaS provider of health benefits comparison tools. We need a new simple SaaS focused website to direct customers to our product

Target Market(s)

General Public comparing their health benefits plans from their employer or from the state exchanges in the US

Coding

Coded - Design and coding required

Number of Pages Required

3 page

Requirements
Must have
• Main page - "Know the Best Health Benefits Plan for You!"
Graphic of a person looking over papers on their desk
Compare Now button to link to SaaS product
About Us
Product Page

https://plimbo.example/top-app-pages/

```html
<!DOCTYPE html>
<html lang="en">
<head>
<meta charset="utf-8">
<title>Veltra Metrics — Know the Best Health Benefits Plan for You</title>
<link href="https://fonts.googleapis.com/css2?family=Cinzel:wght@500;700&family=Mulish:wght@400;500;600&display=swap" rel="stylesheet">
<style>
  :root {
    --page-bg: #eaf7fc;
    --brand-blue: #27a9e1;
    --heading-ink: #2b2f33;
    --body-ink: #333a40;
    --white: #ffffff;
    --art-light: #cfeaf6;
    --art-mid: #8fcbea;
    --art-deep: #4aa6dc;
    --social-1: #3b5a9a;
    --social-2: #d62a2a;
    --social-3: #55acee;
    --social-4: #e31b1b;
  }
  * { box-sizing: border-box; margin: 0; padding: 0; }
  html, body { width: 1200px; height: 600px; overflow: hidden; }
  body {
    position: relative;
    background: var(--page-bg);
    font-family: "Mulish", Arial, sans-serif;
    color: var(--body-ink);
  }
  .site-header { position: absolute; inset: 0 0 auto 0; height: 90px; }
  .brand {
    position: absolute; left: 141px; top: 22px;
    font-family: "Cinzel", Georgia, serif; font-weight: 500;
    font-size: 31px; letter-spacing: 0.5px; color: var(--brand-blue);
    text-decoration: none; white-space: nowrap;
  }
  .main-nav { position: absolute; top: 24px; left: 655px; height: 39px; display: flex; align-items: center; }
  .main-nav a {
    color: var(--body-ink); text-decoration: none;
    font-size: 13px; font-weight: 500; letter-spacing: 0.2px;
    position: absolute; white-space: nowrap;
  }
  .nav-home { left: 0; }
  .nav-about { left: 71px; }
  .nav-product { left: 183px; }
  .btn {
    display: flex; align-items: center; justify-content: center;
    background: var(--brand-blue); color: var(--white);
    font-size: 13px; font-weight: 500; letter-spacing: 0.3px;
    text-decoration: none; border-radius: 3px; white-space: nowrap;
  }
  .main-nav .btn-nav { position: absolute; left: 270px; top: 0; width: 127px; height: 39px; color: var(--white); }
  .hero-title {
    position: absolute; left: 144px; top: 255px;
    font-family: "Cinzel", Georgia, serif; font-weight: 700;
    font-size: 40px; line-height: 51px; color: var(--heading-ink);
    letter-spacing: 0.5px;
  }
  .btn-hero { position: absolute; left: 144px; top: 423px; width: 127px; height: 39px; }
  .hero-art {
    position: absolute; left: 536px; top: 106px; width: 636px; height: 402px;
    border-radius: 48% 52% 40% 46% / 46% 40% 52% 50%;
    background: radial-gradient(ellipse at 55% 50%, var(--art-deep) 0%, var(--art-mid) 35%, var(--art-light) 70%, var(--page-bg) 100%);
  }
  .site-footer { position: absolute; left: 0; right: 0; top: 556px; height: 32px; }
  .copyright { position: absolute; left: 143px; top: 8px; font-size: 13px; }
  .copyright strong { font-weight: 600; }
  .social { position: absolute; left: 926px; top: 2px; display: flex; gap: 7px; list-style: none; }
  .social a { display: block; width: 28px; height: 28px; border-radius: 50%; }
  .social-a { background: var(--social-1); }
  .social-b { background: var(--social-2); }
  .social-c { background: var(--social-3); }
  .social-d { background: var(--social-4); }
</style>
</head>
<body>
  <header class="site-header">
    <a class="brand" href="#">Veltra Metrics</a>
    <nav class="main-nav">
      <a class="nav-home" href="#">HOME</a>
      <a class="nav-about" href="#">ABOUT US</a>
      <a class="nav-product" href="#">PRODUCT</a>
      <a class="btn btn-nav" href="https://plimbo.example/top-app-pages/">COMPARE NOW</a>
    </nav>
  </header>

  <main>
    <h1 class="hero-title">KNOW THE BEST<br>HEALTH BENEFITS<br>PLAN FOR YOU!</h1>
    <a class="btn btn-hero" href="https://plimbo.example/top-app-pages/">COMPARE NOW</a>
    <div class="hero-art" role="img" aria-label="Illustration of people beside a health checklist clipboard, a heart, and an umbrella sheltering a medical shield"></div>
  </main>

  <footer class="site-footer">
    <p class="copyright">Copyright © 2020 <strong>Veltra Metrics LLC.</strong> All Rights Reserved.</p>
    <ul class="social">
      <li><a class="social-a" href="#" aria-label="Social profile 1"></a></li>
      <li><a class="social-b" href="#" aria-label="Social profile 2"></a></li>
      <li><a class="social-c" href="#" aria-label="Social profile 3"></a></li>
      <li><a class="social-d" href="#" aria-label="Social profile 4"></a></li>
    </ul>
  </footer>
</body>
</html>
```